Sleek wordpress site for Bramblecrest finishing works

We are a commercial job shop that serves B2B, govt & LEO and retail clients.We need a wordpress site with 6 individual pages: homepage, coating, laser engraving, laser cutting, part marking, and contact us. I have attached an outline of the desired flow and sub headings for each page. I would like to incorporate the colors of the logo through out the site to be clean and sleek enough to appeal to B2B commercial clients yet be inviting enough for retail clients.

I would like to have easy picture functionality so photographs on each page can be updated easily.

Target Market(s)

B2B industrial & Govt and Military part marking, laser engraving and coating: machine shops, aerospace companies, tool manufactures. Retail: personalized gifts, Job Shop

Coding

Coded - Design and coding required

Font styles to use
Sans Serif
Other font styles liked:
• Open to suggestion

Colors
0255a3
3176b5
eaf1f7
cfdeed
ffffff

Requirements
Must have
• Clean easy to navigate flow, separate pages as indicated on attached outline, high class feel. Great picture functionality, professional and inviting feel,
• **update: needs to be optimized for mobile, should have a gallery function. Gallery can be an additional page or embedded
Nice to have
• Social media connectivity links,
Should not have
• crappy plugins that make back-end management difficult, no blog

```html
<!DOCTYPE html>
<html lang="en">
<head>
<meta charset="utf-8">
<title>Bramblecrest Finishing Works</title>
<link href="https://fonts.googleapis.com/css2?family=Montserrat:wght@700;800&family=Open+Sans:wght@400;600&display=swap" rel="stylesheet">
<style>
:root{
  --brand:#0255a3;
  --brand-deep:#0b3f8f;
  --brand-mid:#3176b5;
  --ice:#eaf1f7;
  --pale:#cfdeed;
  --white:#ffffff;
  --ink:#444444;
  --text:#555555;
  --grey-band:#efefef;
  --footer:#0a3e8e;
  --footer-bar:#0a3a86;
}
*{margin:0;padding:0;box-sizing:border-box}
html,body{width:1200px;height:2525px;overflow:hidden}
body{font-family:"Open Sans",Arial,sans-serif;color:var(--text);background:var(--white);position:relative}
.abs{position:absolute}
.heading{font-family:"Montserrat",Arial,sans-serif;font-weight:800}

/* header */
.site-header{position:absolute;top:0;left:0;width:1200px;height:108px;background:var(--white);border-bottom:3px solid var(--brand-deep)}
.brand{position:absolute;left:100px;top:16px;width:150px;text-align:center}
.brand-mark{width:44px;height:44px;border-radius:50%;background:var(--brand);margin:0 auto 4px}
.brand-name{font-family:"Open Sans",Arial,sans-serif;font-weight:600;font-size:11px;line-height:13px;color:var(--brand)}
.main-nav{position:absolute;right:98px;top:44px;display:flex;gap:39px}
.main-nav a{font-size:13.5px;font-weight:600;color:#333;text-decoration:none;letter-spacing:.2px}
.main-nav a.active{color:var(--brand)}

/* hero */
.hero{position:absolute;top:109px;left:0;width:1200px;height:541px;
  background:radial-gradient(ellipse at 72% 55%,#8a5a48 0%,#3d2f55 25%,transparent 55%),linear-gradient(180deg,#1e1f48 0%,#2a2c5e 50%,#241f3d 100%)}
.hero-title{position:absolute;top:160px;width:100%;text-align:center;font-size:60px;line-height:66px;color:var(--white);letter-spacing:1px;white-space:nowrap}
.hero-sub{position:absolute;top:228px;width:100%;text-align:center;font-size:21px;color:var(--white)}
.hero-btn{position:absolute;left:510px;top:278px;width:180px;height:42px;background:var(--brand);color:var(--white);font-size:18px;font-weight:600;text-align:center;line-height:42px}
.slider-arrow{position:absolute;top:225px}

/* about */
.about{position:absolute;top:650px;left:0;width:1200px;height:447px;background:linear-gradient(180deg,#f4f7fb,#ffffff)}
.about h2{position:absolute;left:100px;top:74px;width:560px;font-size:28px;line-height:34px;color:var(--brand);white-space:nowrap}
.about p{position:absolute;left:100px;top:123px;width:550px;font-size:12.6px;line-height:27px;color:#444}
.btn{position:absolute;background:var(--brand);color:var(--white);font-size:16px;font-weight:600;text-align:center}
.about .btn{left:100px;top:323px;width:159px;height:42px;line-height:42px}
.about-frame{position:absolute;left:687px;top:64px;width:414px;height:310px;border:3px solid var(--brand);border-radius:4px;padding:9px;background:var(--white)}
.about-photo{width:100%;height:100%;background:linear-gradient(135deg,#b0904f 0%,#5e4b2e 45%,#2a2218 100%)}

/* services */
.services{position:absolute;top:1097px;left:0;width:1200px;height:593px;background:var(--grey-band)}
.section-title{position:absolute;width:100%;text-align:center;font-size:40px;color:var(--ink)}
.section-sub{position:absolute;width:100%;text-align:center;font-size:13px;color:#444}
.services .section-title{top:60px}
.services .section-sub{top:118px}
.service-card{position:absolute;top:190px;width:230px;height:312px;background:var(--white);border:1px solid #e0e0e0;text-align:center}
.service-icon{width:112px;height:112px;border-radius:50%;background:var(--brand);border:4px solid var(--white);outline:2px solid var(--brand);margin:22px auto 0}
.service-card h3{font-family:"Montserrat",Arial,sans-serif;font-weight:700;font-size:18px;color:var(--ink);margin-top:18px;letter-spacing:.4px;white-space:nowrap}
.service-card p{font-size:11.6px;line-height:20px;color:#666;padding:0 22px;margin-top:10px}

/* clients */
.clients{position:absolute;top:1690px;left:0;width:1200px;height:379px;background:var(--white)}
.clients .section-title{top:64px}
.clients .section-sub{top:122px}
.client-tile{position:absolute;top:190px;width:190px;height:94px;border:1px solid #cccccc;display:flex;align-items:center;justify-content:center;gap:8px;font-family:"Open Sans",Arial,sans-serif;font-weight:600;font-size:19px;color:#222;white-space:nowrap}
.client-tile .dot{width:14px;height:14px;background:#222}

/* footer */
.site-footer{position:absolute;top:2069px;left:0;width:1200px;height:375px;background:var(--footer);color:var(--white)}
.footer-title{position:absolute;top:58px;font-size:17px;font-weight:600}
.contact-line{position:absolute;left:100px;display:flex;align-items:center;gap:10px;font-size:14px;color:#e3ebf6}
.social{position:absolute;top:249px;width:42px;height:42px;border-radius:50%;background:#5a79b0}
.field{position:absolute;background:var(--white);color:#444;font-size:12.5px;padding:7px 9px}
.send{position:absolute;left:985px;top:287px;width:116px;height:41px;line-height:41px;background:var(--brand-mid);text-align:center;font-weight:600;font-size:16px}
.footer-bar{position:absolute;top:2444px;left:0;width:1200px;height:81px;background:var(--footer-bar);border-top:1px solid #2a57a0;color:#e3ebf6;font-size:12px;text-align:center;line-height:81px}
</style>
</head>
<body>

<header class="site-header">
  <div class="brand">
    <div class="brand-mark"></div>
    <div class="brand-name">BRAMBLECREST<br>FINISHING WORKS</div>
  </div>
  <nav class="main-nav">
    <a class="active" href="#">HOME</a>
    <a href="#">COATING</a>
    <a href="#">LASER ENGRAVING</a>
    <a href="#">LASER CUTTING</a>
    <a href="#">PART MARKING</a>
    <a href="#">CONTACT US</a>
  </nav>
</header>

<section class="hero" role="img" aria-label="Laser cutting machine throwing sparks in a dim workshop">
  <svg class="slider-arrow" style="left:34px" width="20" height="36" viewBox="0 0 20 36"><polyline points="17,2 3,18 17,34" fill="none" stroke="#cfd6e6" stroke-width="2"/></svg>
  <h1 class="hero-title heading">BRAMBLECREST FINISHING</h1>
  <p class="hero-sub">We are commercial job shop that serves B2B, govt and retail clients.</p>
  <div class="hero-btn">LEARN MORE</div>
  <svg class="slider-arrow" style="left:1134px" width="20" height="36" viewBox="0 0 20 36"><polyline points="3,2 17,18 3,34" fill="none" stroke="#cfd6e6" stroke-width="2"/></svg>
</section>

<section class="about">
  <h2 class="heading">ABOUT BRAMBLECREST FINISHING</h2>
  <p>Duraglaze is a spray on ceramic based finish that can be applied to metals, plastics, polymers and wood. The unique formulation used for Duraglaze ceramic coating enhances a number of physical performance properties including abrasion/wear resistance, corrosion resistance, chemical resistance, impact strength, and hardness. Duraglaze ceramic coatings utilize state-of-the-art technology to out-perform any competitive coating in both laboratory settings and real world applications, making it ideal for firearm finishes.</p>
  <div class="btn">LEARN MORE</div>
  <div class="about-frame"><div class="about-photo" role="img" aria-label="Hand guiding material on a laser cutting bed in warm light"></div></div>
</section>

<section class="services">
  <h2 class="section-title heading">OUR SERVICES</h2>
  <p class="section-sub">Contrary to popular belief, Lorem Ipsum is not simply random text.</p>
  <div class="service-card" style="left:100px">
    <div class="service-icon" role="img" aria-label="Laser engraving icon"></div>
    <h3>LASER ENGRAVING</h3>
    <p>Capabilities Statement: With our selection of CO2 and fiber lasers there are very few materials and substrates that we cannot mark or engrave</p>
  </div>
  <div class="service-card" style="left:357px">
    <div class="service-icon" role="img" aria-label="Laser cutting icon"></div>
    <h3>LASER CUTTING</h3>
    <p>Custom cut items can be fabricated from wood, foam packaging, rubber, cardboard, mat board, paper, acrylic and a variety of plastics.</p>
  </div>
  <div class="service-card" style="left:614px">
    <div class="service-icon" role="img" aria-label="Part marking icon"></div>
    <h3>PART MARKING</h3>
    <p>We will sample cut a piece of your material at no charge. Our cutting charges are based on the time required for handling and cutting the material.</p>
  </div>
  <div class="service-card" style="left:871px">
    <div class="service-icon" role="img" aria-label="Spray coating icon"></div>
    <h3>COATINGS</h3>
    <p>Duraglaze ceramic coatings utilize state-of-the-art technology to out-perform any competitive coating in both laboratory settings and real world applications.</p>
  </div>
</section>

<section class="clients">
  <h2 class="section-title heading">OUR CLIENTS</h2>
  <p class="section-sub">Sed ut perspiciatis unde omnis iste natus error sit voluptatem accusantium doloremque</p>
  <svg class="abs" style="left:58px;top:218px" width="20" height="40" viewBox="0 0 20 40"><polyline points="17,2 3,20 17,38" fill="none" stroke="#bbbbbb" stroke-width="2"/></svg>
  <div class="client-tile" style="left:100px"><span class="dot"></span>Northline</div>
  <div class="client-tile" style="left:303px">Lanternwood</div>
  <div class="client-tile" style="left:506px;font-size:17px"><span class="dot"></span>Opencore Guild</div>
  <div class="client-tile" style="left:709px;color:#777;font-size:17px">Hourglass Media</div>
  <div class="client-tile" style="left:912px">Ventrix</div>
  <svg class="abs" style="left:1122px;top:218px" width="20" height="40" viewBox="0 0 20 40"><polyline points="3,2 17,20 3,38" fill="none" stroke="#bbbbbb" stroke-width="2"/></svg>
</section>

<footer class="site-footer">
  <h4 class="footer-title" style="left:100px">Contact us</h4>
  <div class="contact-line" style="top:104px">
    <svg width="11" height="15" viewBox="0 0 11 15"><path d="M5.5 0C2.5 0 0 2.4 0 5.4 0 9.5 5.5 15 5.5 15S11 9.5 11 5.4C11 2.4 8.5 0 5.5 0Zm0 7.5a2 2 0 1 1 0-4 2 2 0 0 1 0 4Z" fill="#e3ebf6"/></svg>
    418 W Copperleaf Ave #7, Tempe, AZ 85281</div>
  <div class="contact-line" style="top:147px">
    <svg width="13" height="13" viewBox="0 0 13 13"><path d="M3 0 5 3 3.6 4.6a8 8 0 0 0 4.8 4.8L10 8l3 2-1.4 2.4C6 13 0 7 .6 1.4Z" fill="#e3ebf6"/></svg>
    480.555.0172</div>
  <div class="contact-line" style="top:190px">
    <svg width="15" height="11" viewBox="0 0 15 11"><rect width="15" height="11" rx="1" fill="#e3ebf6"/><polyline points="0,0 7.5,6 15,0" fill="none" stroke="#0a3e8e" stroke-width="1.4"/></svg>
    hello@bramblecrestworks.com</div>
  <div class="social" style="left:100px" role="img" aria-label="Social link"></div>
  <div class="social" style="left:145px" role="img" aria-label="Social link"></div>
  <div class="social" style="left:191px" role="img" aria-label="Social link"></div>

  <h4 class="footer-title" style="left:565px">Get In Touch</h4>
  <div class="field" style="left:565px;top:100px;width:261px;height:34px">Name</div>
  <div class="field" style="left:841px;top:100px;width:260px;height:34px">Email</div>
  <div class="field" style="left:565px;top:146px;width:536px;height:34px">Phone</div>
  <div class="field" style="left:565px;top:190px;width:536px;height:82px">Message</div>
  <div class="send">SEND</div>
</footer>
<div class="footer-bar">© Copyright-2018 Bramblecrest Finishing. All rights reserved.</div>

</body>
</html>
```